Ridgeline Journeys business card

please see website
www.ridgelinejourneys.comau

info needed on card
Curtis Halvey
Ph
email
Adventure Riding GPS trails

please use my logo and colours off my site

Curtis Halvey
curtis@ridgelinejourneys.com

```html
<!DOCTYPE html>
<html lang="en">
<head>
<meta charset="utf-8">
<title>Ridgeline Journeys – Business Card</title>
<link rel="stylesheet" href="https://fonts.googleapis.com/css2?family=Source+Sans+3:ital,wght@0,400;0,600;0,700;1,400&display=swap">
<style>
  :root {
    --backdrop: #4a4a4a;
    --card: #fbfbfb;
    --ink: #1c1c1c;
    --ink-soft: #3a3a3a;
    --rule: #c9c9c9;
    --accent: #f2c400;
    --band: #050505;
    --band-text: #f4f4f4;
  }
  * { margin: 0; padding: 0; box-sizing: border-box; }
  html, body {
    width: 1200px; height: 750px; overflow: hidden;
    background: var(--backdrop);
    font-family: "Source Sans 3", sans-serif;
  }
  .card {
    position: absolute; left: 40px; top: 55px;
    width: 1120px; height: 640px;
    background: var(--card);
  }
  .brand {
    position: absolute; left: 78px; top: 248px;
    display: flex; align-items: center; gap: 22px;
  }
  .brand-dot {
    width: 70px; height: 70px; border-radius: 50%;
    background: var(--accent);
  }
  .brand-name {
    font-weight: 700; font-size: 44px; line-height: 0.98;
    color: var(--ink); text-transform: uppercase; letter-spacing: 0.5px;
  }
  .divider {
    position: absolute; left: 560px; top: 196px;
    width: 2px; height: 222px; background: var(--rule);
  }
  .contact {
    position: absolute; left: 610px; top: 206px;
  }
  .contact-name {
    font-weight: 600; font-size: 40px; color: var(--ink);
    margin-bottom: 22px;
  }
  .contact-list { list-style: none; }
  .contact-item {
    display: flex; align-items: center; gap: 16px;
    font-size: 27px; color: var(--ink-soft);
    height: 43px;
  }
  .contact-icon { width: 28px; height: 28px; flex: none; fill: var(--ink); }
  .accent-line {
    position: absolute; left: 0; top: 571px;
    width: 100%; height: 6px; background: var(--accent);
  }
  .tagline-band {
    position: absolute; left: 0; top: 577px;
    width: 100%; height: 63px; background: var(--band);
    display: flex; align-items: center; justify-content: center;
  }
  .tagline {
    font-style: italic; font-size: 29px; color: var(--band-text);
    letter-spacing: 0.5px;
  }
</style>
</head>
<body>
  <div class="card">
    <div class="brand">
      <div class="brand-dot"></div>
      <div class="brand-name">Ridgeline<br>Journeys</div>
    </div>

    <div class="divider"></div>

    <div class="contact">
      <div class="contact-name">Curtis Halvey</div>
      <ul class="contact-list">
        <li class="contact-item">
          <svg class="contact-icon" viewBox="0 0 24 24" aria-hidden="true"><path d="M6.6 10.8a15.2 15.2 0 0 0 6.6 6.6l2.2-2.2a1 1 0 0 1 1-.25 11.4 11.4 0 0 0 3.6.57 1 1 0 0 1 1 1V20a1 1 0 0 1-1 1A17 17 0 0 1 3 4a1 1 0 0 1 1-1h3.5a1 1 0 0 1 1 1c0 1.25.2 2.45.57 3.57a1 1 0 0 1-.25 1z"/></svg>
          612 508 7143
        </li>
        <li class="contact-item">
          <svg class="contact-icon" viewBox="0 0 24 24" aria-hidden="true"><path d="M2 5h20v14H2z M4 7v.4l8 5 8-5V7l-8 5z" fill-rule="evenodd"/></svg>
          curtis@ridgelinejourneys.com
        </li>
        <li class="contact-item">
          <svg class="contact-icon" viewBox="0 0 24 24" aria-hidden="true"><circle cx="12" cy="12" r="10"/><path d="M8 6c2 1 1 3 3 3s1 3-1 3-3 2-2 5M15 5c-1 2 1 3 2 4s2 3 0 4-1 4 1 5" fill="none" stroke="#fbfbfb" stroke-width="1.6"/></svg>
          www.ridgelinejourneys.com.au
        </li>
      </ul>
    </div>

    <div class="accent-line"></div>
    <div class="tagline-band">
      <span class="tagline">Adventure Riding GPS trails</span>
    </div>
  </div>
</body>
</html>
```